Black Matte card with samurai logo which I would like it to be textured and company name on one side and on the other side I would like the company information with the reno (Face logo) Sushi logo. Double Sided card.

majority customers are University students, University sororities and fraternities.

It Company

Reno Sushi
317 W. Harlow Ave
Tucson, AZ 85042
Phone (520)413-6271
Fax (520)357-1846
E-mail: Renosushidesert@mailbox-example.com
FB: Renosushidesert
Twitter: Renosushidesert

• Present Normal

```html
<!DOCTYPE html>
<html lang="en">
<head>
<meta charset="utf-8">
<title>Reno Sushi – Business Card</title>
<link href="https://fonts.googleapis.com/css2?family=PT+Sans:wght@400;700&display=swap" rel="stylesheet">
<style>
  :root {
    --page: #ece8e2;
    --card-black: #1c1c1c;
    --card-black-light: #3a3a3a;
    --card-white: #ffffff;
    --brand-red: #b3262a;
    --ink: #2a2a2a;
    --rule: #bdbdbd;
    --band-black: #1e1e1e;
  }
  * { margin: 0; padding: 0; box-sizing: border-box; }
  html, body {
    width: 1200px; height: 983px; overflow: hidden;
    background: var(--page);
    font-family: "PT Sans", Arial, sans-serif;
  }
  .canvas { position: relative; width: 1200px; height: 983px; }

  .card { position: absolute; width: 782px; height: 448px; border-radius: 38px; overflow: hidden; }

  /* Front: textured matte black */
  .card--front {
    left: 370px; top: 22px;
    background:
      repeating-linear-gradient(90deg, rgba(255,255,255,0.025) 0 3px, rgba(0,0,0,0.05) 3px 7px, rgba(255,255,255,0.015) 7px 12px),
      radial-gradient(ellipse at 55% 35%, var(--card-black-light) 0%, var(--card-black) 70%);
  }
  .front-name {
    position: absolute; left: 0; right: 0; top: 160px;
    display: flex; align-items: center; justify-content: center; gap: 22px;
    color: var(--brand-red); font-size: 76px; font-weight: 400; letter-spacing: 1px;
  }
  .brand-dot { width: 44px; height: 44px; border-radius: 50%; background: var(--brand-red); flex: none; }

  /* Back: white info side */
  .card--back {
    left: 88px; top: 522px;
    background: var(--card-white);
    border: 1px solid #999;
  }
  .back-brand {
    position: absolute; left: 110px; top: 90px; width: 210px;
    display: flex; flex-direction: column; align-items: center; gap: 14px;
    color: var(--brand-red); font-size: 48px; line-height: 1; text-align: center;
  }
  .back-brand .brand-dot { width: 70px; height: 70px; }
  .divider { position: absolute; left: 379px; top: 138px; width: 1px; height: 150px; background: var(--rule); }
  .contact-list { position: absolute; left: 397px; top: 140px; list-style: none; }
  .contact-list li {
    display: flex; align-items: center; gap: 10px;
    height: 30px; font-size: 19px; color: var(--ink);
  }
  .contact-icon { width: 19px; height: 19px; flex: none; }
  .social-square { width: 17px; height: 17px; border-radius: 3px; background: var(--brand-red); flex: none; margin: 0 1px; }
  .bottom-band { position: absolute; left: 0; bottom: 0; width: 782px; height: 66px; }
  .address {
    position: absolute; right: 12px; bottom: 18px;
    color: #fff; font-size: 18px;
  }
</style>
</head>
<body>
<main class="canvas">

  <section class="card card--front" aria-label="Card front">
    <div class="front-name"><span class="brand-dot"></span><span>Reno Sushi</span></div>
  </section>

  <section class="card card--back" aria-label="Card back">
    <div class="back-brand"><span class="brand-dot"></span><span>Reno Sushi</span></div>

    <div class="divider"></div>

    <ul class="contact-list">
      <li>
        <svg class="contact-icon" viewBox="0 0 20 20"><circle cx="10" cy="10" r="8.5" fill="none" stroke="#b3262a" stroke-width="1.6"/><path d="M7 5.5c-1.5 1.5-.8 4.3 1.3 6.6s4.8 3 6.2 1.7l-1.6-2-1.5.9c-1-.5-2.4-2-2.8-3l1-1.4z" fill="#b3262a"/></svg>
        <span>(520)413-6271</span>
      </li>
      <li>
        <svg class="contact-icon" viewBox="0 0 20 20"><rect x="5" y="2" width="10" height="16" rx="1.5" fill="#b3262a"/><rect x="7" y="4" width="6" height="5" fill="#fff"/><rect x="7" y="11" width="6" height="5" fill="#fff" opacity=".5"/></svg>
        <span>(520)357-1846</span>
      </li>
      <li>
        <svg class="contact-icon" viewBox="0 0 20 20"><rect x="1" y="5" width="18" height="11" rx="1" fill="#b3262a"/><path d="M1.5 5.5L10 11l8.5-5.5" fill="none" stroke="#fff" stroke-width="1.4"/></svg>
        <span>Renosushidesert@mailbox-example.com</span>
      </li>
      <li><span class="social-square"></span><span>Renosushidesert</span></li>
      <li><span class="social-square"></span><span>Renosushidesert</span></li>
    </ul>

    <svg class="bottom-band" viewBox="0 0 782 66" preserveAspectRatio="none" aria-hidden="true">
      <polygon points="0,0 343,0 327,22 0,22" fill="#b3262a"/>
      <polygon points="0,30 320,30 345,0 782,0 782,66 0,66" fill="#1e1e1e"/>
    </svg>
    <p class="address">Reno Sushi 317 W. Harlow Ave Tucson, AZ 85042</p>
  </section>

</main>
</body>
</html>
```